Talon Microsystems PowerPoint Master Slide Deck Design

This is a 2-phase project to design a slide deck for a semiconductor company in the Silicon Valley. The design budget will be increased with each phase.
The slide deck will need to have one version with a dark background for presentations and a second version with a white background. Otherwise, the slides will be the same. I anticipate we will need a total of 10 slides, but that number may change.
The first phase will be to design a Title and a Title and Content slide.
- The Title Slide is the first slide of the deck. It should include the presentation title, the presenter's name and date of presentation
- The Title and Content slide should include a title and content with bullet points and up to 2 additional sub-bullets
- The Title and Content slide should have a footer that includes the slide #, Talon Microsystems Confidential, and the logo. This footer will be on every slide except the Title Slide
The first two slides will serve as the format for the remaining ~8 slides:
-Header and Content Text (1, 2, 4 column)
-Header and Content Image (bar chart, pie chart, tables)
-Break
-Title only
-Closing (Talon logo only)
Our slides contain a lot of content so a clean and simple design is best.
Both phases will need to include pre-set color options for
-Text and Lines
-Shadows
-Bullets and sub-bullets (including shapes, ex. circle, slash, square, etc.)
-Bar charts, pie charts, tables
Samples of our collateral are attached. Logo files are also attached
Look and feel
Each slider illustrates characteristics of the customer's brand and the style your logo design should communicate.

```html
<!DOCTYPE html>
<html lang="en">
<head>
<meta charset="utf-8">
<title>Talon Microsystems Slide Master</title>
<link rel="stylesheet" href="https://fonts.googleapis.com/css2?family=PT+Serif:wght@400;700&display=swap">
<style>
:root{
  --sheet:#dcdcdc;
  --white:#ffffff;
  --ink:#111418;
  --navy-deep:#06163f;
  --navy:#0d2f7a;
  --blue-royal:#3a5cf5;
  --blue:#1a6ff5;
  --blue-sky:#0aa3f5;
  --accent:#16a4ee;
  --charcoal:#3b3b3d;
  --muted:#9aa3ad;
}
*{box-sizing:border-box;margin:0;padding:0}
html,body{width:1200px;height:4046px;overflow:hidden;background:var(--sheet)}
body{font-family:"PT Serif",Georgia,serif;color:var(--ink);position:relative}
.slide{position:absolute;left:52px;width:1096px;height:617px;background:var(--white);overflow:hidden}
.abs{position:absolute}
.page-no{position:absolute;font-size:13px}
.heading{position:absolute;font-weight:700;font-size:30px;letter-spacing:.5px}
.heading-rule{position:absolute;height:4px;width:100px;background:var(--accent)}
.brand{position:absolute;display:flex;align-items:center;gap:12px}
.brand-dot{width:34px;height:34px;border-radius:50%;background:var(--blue)}
.brand-name{font-weight:700;font-size:26px;color:var(--blue);white-space:nowrap}
.footer-band{position:absolute;background:var(--accent);color:var(--white);font-weight:700;font-size:18px;letter-spacing:.5px;display:flex;align-items:center}
.footer-band .page-no{color:var(--white);font-weight:400}
.footer-band .brand-dot{width:20px;height:20px;background:var(--white)}
.footer-band .brand-name{font-size:16px;color:var(--white)}

/* slide 1 */
.s-title{top:36px;background:linear-gradient(140deg,var(--navy-deep),var(--navy) 55%,#0a2566)}
.s-title .deck-title{left:66px;top:188px;font-size:42px;font-weight:700;color:var(--white);letter-spacing:.5px}
.s-title .presenter{left:82px;top:458px;font-size:28px;font-weight:700;color:var(--white);letter-spacing:1px}
.s-title .date{left:82px;top:506px;font-size:14px;font-weight:700;color:var(--white)}
.s-title .page-no{left:1064px;top:572px;color:var(--white)}

/* slide 2 */
.s-services{top:685px}
.flow{position:absolute;left:122px;top:176px;width:852px;height:250px}
.flow-box{position:absolute;top:0;width:245px;height:248px;border:1.5px solid var(--blue);border-bottom:1.5px dotted var(--blue);border-radius:4px}
.flow-card{position:absolute;left:10px;top:16px;right:10px;bottom:16px;border:4px solid #e3e5ea;border-radius:6px;box-shadow:0 2px 4px rgba(0,0,0,.2);color:var(--white);padding:14px 16px}
.flow-card h3{font-size:14px;text-align:center;margin-bottom:10px}
.flow-card p{font-size:8.5px;line-height:14px;padding-left:18px;position:relative;margin-bottom:10px}
.flow-card p::before{content:"";position:absolute;left:2px;top:3px;width:7px;height:7px;border:1px solid rgba(255,255,255,.8);transform:rotate(45deg)}
.flow-arrow{position:absolute;top:112px;width:56px;height:24px}

/* slide 3 */
.s-about{top:1356px}
.s-about .body-copy{left:612px;top:240px;width:430px;font-size:12.5px;line-height:26px;letter-spacing:.3px}
.s-about .body-copy p{margin-bottom:6px}

/* slide 4 */
.s-who{top:2032px}
.bullets{position:absolute;left:52px;top:162px;width:1020px;list-style:none;font-size:12.5px;line-height:26px;letter-spacing:.3px}
.bullets>li{position:relative;padding-left:34px;margin-bottom:14px}
.bullets>li::before{content:"";position:absolute;left:8px;top:9px;width:9px;height:9px;border:1.5px solid var(--accent);transform:rotate(45deg)}
.sub-bullets{list-style:none;margin-top:6px}
.sub-bullets li{position:relative;padding-left:54px;margin-bottom:6px}
.sub-bullets li::before{content:"";position:absolute;left:36px;top:9px;width:8px;height:8px;border-radius:50%;background:var(--accent)}

/* slide 5 */
.s-break{top:2702px}
.s-break .big-title{left:86px;top:222px;font-size:52px;font-weight:700;letter-spacing:.5px}

/* slide 6 */
.s-close{top:3380px}
.s-close .page-no{left:1060px;top:572px}
</style>
</head>
<body>

<!-- Title slide -->
<section class="slide s-title">
  <div class="abs" role="img" aria-label="Dark blue digital network background" style="inset:0"></div>
  <svg class="abs" style="left:0;top:0" width="1096" height="617" viewBox="0 0 1096 617">
    <circle cx="890" cy="280" r="310" fill="var(--charcoal)"/>
    <circle cx="935" cy="250" r="292" fill="var(--white)"/>
    <circle cx="945" cy="245" r="272" fill="#1557b8"/>
  </svg>
  <div class="abs" role="img" aria-label="Close-up photo of a blue circuit board with a microchip" style="left:673px;top:-27px;width:544px;height:544px;border-radius:50%;background:radial-gradient(circle at 60% 30%,#2fa6ff,#0d5cc4 45%,#06235e 90%)"></div>
  <h1 class="abs deck-title">Talon Microsystems</h1>
  <p class="abs presenter">Name: Clara Whitfield</p>
  <p class="abs date">Date: December 12,2023</p>
  <span class="page-no">1</span>
</section>

<!-- Services -->
<section class="slide s-services">
  <h2 class="heading" style="left:79px;top:60px">Services</h2>
  <div class="heading-rule" style="left:80px;top:105px"></div>
  <div class="brand" style="left:790px;top:60px"><span class="brand-dot"></span><span class="brand-name">Talon Microsystems</span></div>
  <div class="flow">
    <div class="flow-box" style="left:0"><div class="flow-card" style="background:var(--blue-royal)"><h3>Lorem Ipsum</h3><p>Lorem ipsum dolor sit amet, consectetur adipiscing elit, sed do eiusmod tempor incididunt ut labore et dolore magna aliqua</p><p>Lorem ipsum dolor sit amet, consectetur adipiscing elit, sed do eiusmod tempor incididunt ut labore et dolore magna aliqua</p></div></div>
    <svg class="flow-arrow" style="left:250px" viewBox="0 0 56 24"><path d="M2 12H52M42 2l10 10-10 10" fill="none" stroke="var(--blue)" stroke-width="2"/></svg>
    <div class="flow-box" style="left:304px"><div class="flow-card" style="background:var(--blue)"><h3>Lorem Ipsum</h3><p>Lorem ipsum dolor sit amet, consectetur adipiscing elit, sed do eiusmod tempor incididunt ut labore et dolore magna aliqua</p><p>Lorem ipsum dolor sit amet, consectetur adipiscing elit, sed do eiusmod tempor incididunt ut labore et dolore magna aliqua</p></div></div>
    <svg class="flow-arrow" style="left:554px" viewBox="0 0 56 24"><path d="M2 12H52M42 2l10 10-10 10" fill="none" stroke="var(--blue)" stroke-width="2"/></svg>
    <div class="flow-box" style="left:608px"><div class="flow-card" style="background:var(--blue-sky)"><h3>Lorem Ipsum</h3><p>Lorem ipsum dolor sit amet, consectetur adipiscing elit, sed do eiusmod tempor incididunt ut labore et dolore magna aliqua</p><p>Lorem ipsum dolor sit amet, consectetur adipiscing elit, sed do eiusmod tempor incididunt ut labore et dolore magna aliqua</p></div></div>
  </div>
  <div class="footer-band" style="left:500px;top:559px;width:596px;height:58px;clip-path:polygon(40px 0,100% 0,100% 100%,0 100%);padding-left:122px">
    Talon Microsystems Confidential<span class="page-no" style="left:530px">2</span>
  </div>
</section>

<!-- About -->
<section class="slide s-about">
  <div class="abs" role="img" aria-label="Photo of a silicon wafer under blue-lit inspection equipment" style="left:0;top:0;width:600px;height:617px;background:radial-gradient(ellipse at 45% 60%,#5fd0ff,#1a6fc8 40%,#0a2a5a 80%)"></div>
  <svg class="abs" style="left:0;top:0" width="1096" height="617" viewBox="0 0 1096 617">
    <path d="M565 0C470 90 500 200 540 300C580 400 560 520 520 617H1096V0Z" fill="var(--white)"/>
    <path d="M600 30C520 110 530 210 565 300C600 390 590 520 545 612C580 540 596 430 572 330C548 230 540 120 600 30Z" fill="var(--blue)"/>
  </svg>
  <div class="brand" style="left:832px;top:48px"><span class="brand-dot"></span><span class="brand-name" style="font-size:22px">Talon Microsystems</span></div>
  <h2 class="heading" style="left:612px;top:160px">About</h2>
  <div class="heading-rule" style="left:612px;top:207px"></div>
  <div class="abs body-copy">
    <p>Lorem ipsum dolor sit amet, consectetur adipiscing elit, sed do eiusmod tempor incididunt ut labore et dolore magna aliqua. Ut enim ad minim veniam, quis nostrud exercitation ullamco laboris nisi ut aliquip ex ea commodo consequat. Duis aute irure dolor in reprehenderit in voluptate velit esse cillum dolore eu fugiat nulla pariatur</p>
    <p>Lorem ipsum dolor sit amet, consectetur adipiscing elit, sed do eiusmod tempor incididunt ut labore et dolore magna aliqua. Ut enim ad minim veniam, quis nostrud exercitation ullamco laboris nisi ut aliquip ex ea commodo consequat.</p>
  </div>
  <div class="footer-band" style="left:609px;top:561px;width:487px;height:60px;clip-path:polygon(36px 0,100% 0,100% 100%,0 100%);padding-left:38px">
    Talon Microsystems Confidential
    <span class="brand-dot abs" style="left:400px;top:20px"></span>
    <span class="page-no" style="left:450px">3</span>
  </div>
</section>

<!-- Who We Are -->
<section class="slide s-who">
  <h2 class="heading" style="left:52px;top:60px">Who We Are</h2>
  <div class="heading-rule" style="left:52px;top:106px"></div>
  <div class="brand" style="left:817px;top:42px"><span class="brand-dot"></span><span class="brand-name" style="font-size:22px">Talon Microsystems</span></div>
  <ul class="bullets">
    <li>Lorem ipsum dolor sit amet, consectetur adipiscing elit, sed do eiusmod tempor incididunt ut labore et dolore magna aliqua. Ut enim ad minim veniam, quis nostrud exercitation ullamco laboris nisi ut aliquip ex ea commodo consequat. Duis aute irure dolor in reprehenderit in voluptate velit esse cillum dolore eu fugiat nulla pariatur</li>
    <li>Lorem ipsum dolor sit amet, consectetur adipiscing elit, sed do eiusmod tempor incididunt ut labore et dolore magna aliqua. Ut enim ad minim veniam, quis nostrud exercitation ullamco laboris nisi ut aliquip ex ea commodo consequat.</li>
    <li>Sed ut perspiciatis unde omnis iste natus error sit voluptatem accusantium doloremque laudantium, totam rem aperiam, eaque ipsa quae ab illo inventore veritatis et quasi architecto beatae vitae dicta sunt explicabo. Nemo enim ipsam voluptatem quia voluptas sit
      <ul class="sub-bullets">
        <li>Lorem ipsum dolor sit amet, consectetur adipiscing elit, sed do eiusmod tempor incididunt ut labore</li>
        <li>Lorem ipsum dolor sit amet, consectetur adipiscing elit, sed do eiusmod tempor incididunt ut labore</li>
      </ul>
    </li>
    <li>Ut enim ad minima veniam, quis nostrum exercitationem ullam corporis suscipit laboriosam, nisi ut aliquid ex ea commodi consequatur? Quis autem vel eum iure reprehenderit qui in ea voluptate velit esse quam nihil molestiae consequatur, vel illum qui</li>
  </ul>
  <div class="footer-band" style="left:0;top:555px;width:520px;height:62px;clip-path:polygon(0 0,482px 0,100% 100%,0 100%);padding-left:16px;gap:26px">
    <span class="brand"><span class="brand-dot"></span><span class="brand-name">Talon</span></span>
    <span style="margin-left:96px">Talon Microsystems Confidential</span>
  </div>
</section>

<!-- Break -->
<section class="slide s-break">
  <div class="brand" style="left:44px;top:64px"><span class="brand-dot"></span><span class="brand-name">Talon Microsystems</span></div>
  <h2 class="abs big-title">Talon Microsystems</h2>
  <svg class="abs" style="left:760px;top:80px" width="320" height="320" viewBox="0 0 320 320">
    <path d="M170 6A154 154 0 1 0 176 314A150 150 0 1 1 170 6Z" fill="var(--blue)"/>
    <circle cx="170" cy="160" r="148" fill="none" stroke="var(--accent)" stroke-width="1.5"/>
  </svg>
  <div class="abs" role="img" aria-label="Glowing blue and gold circuit board landscape" style="left:785px;top:95px;width:290px;height:290px;border-radius:50%;background:radial-gradient(circle at 50% 70%,#f2b54a,#1b4f9e 45%,#071a3d 85%)"></div>
  <div class="footer-band" style="left:529px;top:550px;width:567px;height:67px;clip-path:polygon(30px 0,100% 0,100% 100%,0 100%);padding-left:36px">
    Talon Microsystems Confidential
    <span class="brand abs" style="left:380px;top:22px"><span class="brand-dot"></span><span class="brand-name">Talon</span></span>
    <span class="page-no" style="left:530px">5</span>
  </div>
</section>

<!-- Closing -->
<section class="slide s-close">
  <svg class="abs" style="left:0;top:0" width="1096" height="617" viewBox="0 0 1096 617">
    <path d="M555 0C520 50 508 110 508 172C514 110 530 50 560 0Z" fill="var(--blue)"/>
    <path d="M582 440C590 500 580 560 560 617C598 560 604 500 590 440Z" fill="var(--blue)"/>
    <circle cx="552" cy="306" r="134" fill="var(--white)" stroke="var(--accent)" stroke-width="1.5"/>
  </svg>
  <div class="brand" style="left:448px;top:290px"><span class="brand-dot" style="width:26px;height:26px"></span><span class="brand-name" style="font-size:20px">Talon Microsystems</span></div>
  <span class="page-no">7</span>
</section>

</body>
</html>
```